Fresh, modern, fun business card for pediatric dental practice

Need a business card for fresh, modern, fun pediatric dental practice

Clean look that matches our website's font and colors

We prefer the look of curved corners on business cards

Target Market(s)

parents (mothers) of young children, professionals, mid-high class

Industry/Entity Type

Dental

Contact Information for Business Card

Maplebrook Pediatric Dentistry
482 Quarry Lane
Suite 517
Cedar Glen, PA 17990
717.555.0193
www.maplebrookkidsdental.example

Mei-Ran Tsai, DMD
Corinne Walbeck, DMD
(we are working on our email address, but we would like that on the card as well)

Font styles to use
Sans Serif

Requirements
Must have
• All info; we would also like to make cards for individual staff members
• colors from our website and color palatte, attatched
• use same font and design as website for branding
Nice to have
• clean, simple card that has a pop of color
• we would like to see a few designs with our tag line "where smiles get brighter"
• we are not sure if we want to have it on there or not
• we would like to see a few designs incorporating the ribbon graphic on our website where the word WELCOME is

```html
<!DOCTYPE html>
<html lang="en">
<head>
<meta charset="utf-8">
<title>Maplebrook Pediatric Dentistry – Business Card</title>
<link rel="stylesheet" href="https://fonts.googleapis.com/css2?family=Open+Sans:wght@400;600;700&family=Roboto+Condensed:wght@500&display=swap">
<style>
  :root {
    --backdrop: #2c2c2c;
    --pink: #d4338f;
    --yellow: #f8bc2a;
    --paper: #f4f4f4;
    --ink: #555555;
    --white: #ffffff;
  }
  * { margin: 0; padding: 0; box-sizing: border-box; }
  html, body { width: 1200px; height: 960px; overflow: hidden; }
  body { background: var(--backdrop); font-family: "Open Sans", Arial, sans-serif; position: relative; }

  .card { position: absolute; left: 320px; width: 600px; border-radius: 20px; overflow: hidden; }

  /* Front */
  .card-front { top: 105px; height: 345px; background: var(--pink); }
  .front-mark { position: absolute; left: 0; right: 0; top: 105px; text-align: center; }
  .front-mark .dot { display: block; width: 80px; height: 80px; margin: 0 auto 18px; border-radius: 50%; background: var(--yellow); }
  .front-mark .name { font-size: 28px; font-weight: 600; color: var(--yellow); }
  .front-url { position: absolute; left: 0; right: 0; top: 296px; text-align: center; color: var(--white);
    font-size: 13px; letter-spacing: 3.2px; }

  /* Back */
  .card-back { top: 493px; height: 342px; background: var(--paper); }
  .back-swoosh { position: absolute; inset: 0; width: 600px; height: 342px; }

  .brand { position: absolute; left: 36px; top: 38px; color: var(--yellow); font-weight: 700; line-height: 1.05; }
  .brand .dot { display: block; width: 36px; height: 36px; border-radius: 50%; background: var(--yellow); margin: 0 0 12px 86px; }
  .brand .line1 { display: block; font-size: 34px; letter-spacing: 0.5px; }
  .brand .line2 { display: block; font-size: 20px; margin-top: 4px; }

  .doctors { position: absolute; right: 78px; top: 104px; text-align: right;
    font-family: "Roboto Condensed", "Arial Narrow", sans-serif; font-weight: 500;
    font-size: 20px; line-height: 24px; color: var(--yellow); text-transform: uppercase; }

  .contact { position: absolute; left: 36px; top: 204px; font-size: 14px; line-height: 19px; color: var(--ink); }
  .contact .row { display: flex; align-items: center; gap: 6px; }
  .contact svg { width: 14px; height: 14px; fill: var(--yellow); flex: none; }
  .contact address { font-style: normal; margin-top: 6px; }
</style>
</head>
<body>

<section class="card card-front">
  <div class="front-mark">
    <span class="dot"></span>
    <span class="name">Maplebrook</span>
  </div>
  <p class="front-url">www.maplebrookkidsdental.example</p>
</section>

<section class="card card-back">
  <svg class="back-swoosh" viewBox="0 0 600 342" aria-hidden="true">
    <path d="M474,0 C545,50 562,150 550,215 C540,270 510,310 472,342 L600,342 L600,0 Z" fill="var(--yellow)"/>
    <path d="M312,342 C430,310 528,245 545,130 C552,222 520,300 464,342 Z" fill="var(--pink)"
          stroke="var(--paper)" stroke-width="5" stroke-linejoin="round" paint-order="stroke"/>
  </svg>

  <div class="brand">
    <span class="dot"></span>
    <span class="line1">Maplebrook</span>
    <span class="line2">Pediatric Dentistry</span>
  </div>

  <div class="doctors">
    <p>Mei-Ran Tsai, DMD</p>
    <p>Corinne Walbeck, DMD</p>
  </div>

  <div class="contact">
    <p class="row">
      <svg viewBox="0 0 24 24"><path d="M6.6 10.8c1.4 2.8 3.8 5.1 6.6 6.6l2.2-2.2c.3-.3.7-.4 1-.2 1.1.4 2.3.6 3.6.6.6 0 1 .4 1 1V20c0 .6-.4 1-1 1C10.6 21 3 13.4 3 4c0-.6.4-1 1-1h3.5c.6 0 1 .4 1 1 0 1.3.2 2.5.6 3.6.1.3 0 .7-.2 1L6.6 10.8z"/></svg>
      717.555.0193
    </p>
    <p class="row">
      <svg viewBox="0 0 24 24"><path d="M12 2a10 10 0 1 0 0 20 10 10 0 0 0 0-20zm0 2c1 0 2.3 1.9 2.8 5H9.2C9.7 5.9 11 4 12 4zM4.3 11h4.7c0 .7 0 1.4.1 2H4.3a8 8 0 0 1 0-2zm.6 4h4.4c.3 1.6.8 3 1.4 3.9A8 8 0 0 1 4.9 15zm4.3-6H4.9a8 8 0 0 1 5.8-3.9C10 6 9.5 7.4 9.2 9zM12 20c-1 0-2.300-1.9-2.8-5h5.6c-.5 3.1-1.8 5-2.8 5zm3-7h-6a17 17 0 0 1 0-2h6a17 17 0 0 1 0 2zm-1.7 5.9c.6-.9 1.1-2.3 1.4-3.9h4.4a8 8 0 0 1-5.8 3.9zM15 11h4.7a8 8 0 0 1 0 2H15c.1-.6.1-1.3 0-2zm-.2-2c-.3-1.6-.8-3-1.4-3.900A8 8 0 0 1 19.1 9h-4.3z"/></svg>
      maplebrookkidsdental.example
    </p>
    <address>
      Maplebrook Pediatric Dentistry<br>
      482 Quarry Lane<br>
      Suite 517, Cedar Glen, PA 17990
    </address>
  </div>
</section>

</body>
</html>
```